Re-design and craft the perfect CV platform

We are building a CV-based platform designed to connect employees and employers, with a strong focus on individual users. As we're just starting out, we're looking to have our platform and logo redesigned to better reflect our vision
https://app.zelvorhire.com/
Colors like in the logo attached
#87C032 #6A6E71 #618930 - also you can add more colors if you like.
https://app.zelvorhire.com/dashboard - This page would be nice if you plan it, like personal Bio dashboard. Attached picture (Dashboard wanted) one idea from how we would like to be, but we are open for new professional ideas/solutions.
https://app.zelvorhire.com/posts - On this page we want to be showed the jobs posted. Attached one picture about our idea (jobs page wanted)
https://app.zelvorhire.com/profile - design something nice.
Only Photoshop, Illustrator or Figma
Other pictures from the app attached (as looking right now)

Target Market(s)

Job seekers, HR, Recruiters

Industry/Entity Type

HR Tech

Number of Pages Required

5+ page

Colors
00AB8E
00BBA5
67D7C9
C6EFE9
E9F9F6

```html
<!DOCTYPE html>
<html lang="en">
<head>
<meta charset="utf-8">
<title>Zelvor – Recruitment Web App Screens</title>
<link href="https://fonts.googleapis.com/css2?family=Poppins:wght@400;500;600;700;800&display=swap" rel="stylesheet">
<style>
:root{
  --green:#87C032;
  --green-dark:#618930;
  --gray:#6A6E71;
  --stage:#676b6e;
  --ink:#54585b;
  --ink-soft:#8a8e91;
  --line:#e3e3e3;
  --panel:#ffffff;
  --body:#e9e9e9;
  --header:#f1f1f1;
}
*{margin:0;padding:0;box-sizing:border-box}
html,body{width:1200px;height:2576px;overflow:hidden}
body{background:var(--stage);font-family:"Poppins",sans-serif;color:var(--ink);position:relative}
.stage-decor{position:absolute;left:0;top:1290px;width:1200px;height:1286px;
  background:linear-gradient(180deg,rgba(135,192,50,0) 0%,rgba(135,192,50,.28) 35%,rgba(135,192,50,.45) 70%,rgba(135,192,50,.55) 100%)}
.section-title{position:absolute;left:178px;font-size:30px;font-weight:800;color:#fff;letter-spacing:-.5px;line-height:1}
.screen{position:absolute;left:180px;width:840px;height:501px;border:6px solid #fff;border-radius:12px;overflow:hidden}

/* brand */
.brand{position:absolute;text-align:center;font-weight:600;color:var(--green);letter-spacing:1px}
.brand-lg{width:120px;font-size:24px}
.brand-sm{font-size:14px}

/* login */
.login-bg-1{background:linear-gradient(180deg,#e4e4e4 0%,#dedede 60%,#d6d6d6 100%)}
.login-bg-2{background:linear-gradient(135deg,#eef3f7 0%,#ffffff 55%,#ffffff 100%)}
.login-card{position:absolute;width:260px;height:265px;background:#fff;border-radius:20px;padding:19px 22px}
.login-card.outlined{border:1px solid #b9dd8a;box-shadow:0 10px 30px rgba(0,0,0,.06)}
.login-card h2{font-size:12.5px;font-weight:600;color:#5b5f62}
.login-card h2 span{color:var(--green)}
.login-card hr{border:0;border-top:1px solid var(--line);margin:12px 0 20px}
.login-card h3{font-size:10px;font-weight:500;color:#5b5f62}
.login-card p{font-size:7px;line-height:11.5px;color:var(--ink-soft);margin-top:8px}
.field-label{display:block;font-size:6.5px;font-weight:600;color:#5b5f62;margin-top:19px}
.field-label em{color:#e04b4b;font-style:normal}
.input{display:flex;align-items:center;gap:7px;height:30px;border-radius:15px;background:#efefef;margin-top:6px;padding:0 15px;font-size:7px;color:#8d9093}
.btn-continue{position:relative;display:flex;align-items:center;justify-content:center;height:30px;border-radius:15px;background:var(--green);margin-top:13px;font-size:7.5px;font-weight:600;color:#fff}
.btn-continue i{position:absolute;right:4px;top:4px;width:22px;height:22px;border-radius:50%;background:#fff;display:flex;align-items:center;justify-content:center}
.photo{position:absolute}

/* app chrome */
.app{background:var(--body)}
.app-header{position:absolute;left:0;top:0;width:828px;height:58px;background:var(--header)}
.app-header .divider{position:absolute;left:101px;top:12px;width:1px;height:32px;background:#d6d6d6}
.app-header .title{position:absolute;left:116px;top:20px;font-size:12.5px;font-weight:700;color:#5b5f62}
.app-header .title span{color:var(--green)}
.pill{position:absolute;top:18px;height:23px;width:59px;border:1px solid #a9acaf;border-radius:12px;display:flex;align-items:center;justify-content:center;gap:4px;font-size:7.5px;color:#5b5f62}
.hicon{position:absolute;top:23px}

.card{position:absolute;top:65px;height:403px;background:var(--panel);border-radius:8px}

/* profile sidebar */
.side{left:20px;width:154px;padding:16px 19px 0}
.avatar{width:94px;height:94px;border-radius:50%;border:2px solid #b7d88a;padding:3px;margin:0 auto 8px}
.avatar div{width:100%;height:100%;border-radius:50%;background:radial-gradient(circle at 50% 40%,#b59a88 0%,#6f6a68 55%,#3e4a55 100%)}
.side .name{text-align:center;font-size:11.5px;font-weight:600;color:#5b5f62;line-height:14px}
.side .email{text-align:center;font-size:6.5px;color:var(--ink-soft);line-height:10px;margin-bottom:14px}
.facts{display:grid;grid-template-columns:40px 1fr;font-size:6.5px;line-height:14px}
.facts dt{font-weight:600;color:#5b5f62}
.facts dd{color:var(--ink-soft)}
.side hr{border:0;border-top:1px solid var(--line);margin:8px 0 10px}
.side h4{font-size:7px;font-weight:600;color:#5b5f62;line-height:12px}
.side .val{font-size:6.5px;color:var(--ink-soft);line-height:10px}
.lang{margin-top:9px}
.lang .lbl{display:flex;justify-content:space-between;font-size:6.5px;color:var(--ink-soft);line-height:10px}
.bar{height:4px;border-radius:2px;background:#e4e4e4;margin-top:2px;overflow:hidden}
.bar b{display:block;height:100%;background:repeating-linear-gradient(90deg,var(--green) 0 3px,#9fd15a 3px 4px)}

/* bio */
.bio{left:190px;width:448px;padding:18px 20px}
.bio h4{font-size:7.5px;font-weight:700;color:#5b5f62;text-transform:uppercase;line-height:12px}
.bio p,.bio li,.bio .txt{font-size:6.5px;color:var(--ink-soft);line-height:10.5px}
.bio hr{border:0;border-top:1px solid var(--line);margin:9px 0 12px}
.badge{display:inline-block;background:var(--green);color:#fff;border-radius:8px;font-size:5.5px;font-weight:600;padding:2px 7px;margin-left:4px;vertical-align:1px}
.bio ul{list-style:none;margin-top:3px}
.bio li{position:relative;padding-left:10px;display:grid;line-height:12.5px}
.bio li::before{content:"";position:absolute;left:1px;top:4px;width:4px;height:4px;border-radius:50%;background:var(--green)}
.edu li{grid-template-columns:171px 1fr}
.skills li{grid-template-columns:113px 1fr;line-height:13px}
.edu li span:first-child,.skills li span:first-child{color:#5b5f62}

/* my jobs */
.myjobs{left:653px;width:154px;padding:18px 17px}
.myjobs h4{font-size:7.5px;font-weight:700;color:#5b5f62;line-height:12px}
.tabs{display:flex;gap:13px;font-size:6.5px;color:#5b5f62;margin-top:8px;border-bottom:1px solid var(--line)}
.tabs span{padding-bottom:3px}
.tabs .on{color:var(--green);border-bottom:2px solid var(--green)}
.saved{position:relative;margin-top:20px;height:89px}
.saved .logo{position:absolute;left:1px;top:0;width:28px;height:28px;border-radius:50%;background:#f1f1f1;display:flex;align-items:center;justify-content:center}
.saved .t{position:absolute;left:36px;top:6px;font-size:6.5px;font-weight:600;color:#5b5f62;line-height:9px}
.saved .d{position:absolute;left:36px;top:14px;font-size:5px;color:var(--ink-soft)}
.saved .more{position:absolute;right:0;top:8px}
.saved p{position:absolute;left:0;top:35px;width:118px;font-size:6px;color:var(--ink-soft);line-height:9.5px}
.saved .btns{position:absolute;left:0;top:59px;display:flex;gap:3px}
.mini{height:14px;width:42px;border-radius:7px;display:flex;align-items:center;justify-content:center;font-size:5px;font-weight:700;color:#fff}
.mini.apply{background:var(--green)}
.mini.view{background:#686c6f}

/* jobs list */
.jobs-main{left:190px;width:617px}
.search{position:absolute;left:21px;top:21px;width:188px;height:25px;border-radius:13px;background:#f1f1f1;display:flex;align-items:center;justify-content:space-between;padding:0 12px;font-size:6px;color:#9a9da0}
.tools{position:absolute;left:462px;top:22px;display:flex;gap:5px}
.tools span{width:23px;height:23px;border-radius:50%;border:1px solid #cfd1d3;display:flex;align-items:center;justify-content:center}
.tools .on{background:var(--green);border-color:var(--green)}
.joblist{position:absolute;left:21px;top:74px;width:574px;height:291px;background:#f5f5f5;border-radius:8px}
.job{position:relative;height:58px;border-radius:6px}
.job.hl{background:#eff5e6;border:1px solid #b9dd8a}
.job .logo{position:absolute;left:13px;top:10px;width:38px;height:38px;border-radius:50%;background:#fff;border:1px solid #e4e4e4;display:flex;align-items:center;justify-content:center}
.job .logo b{width:14px;height:14px;border-radius:50%;background:var(--c)}
.job .co{position:absolute;left:58px;top:17px;font-size:6.5px;color:var(--ink-soft);line-height:10px}
.job .role{position:absolute;left:58px;top:29px;font-size:7px;font-weight:600;color:#5b5f62;line-height:10px}
.job .meta{position:absolute;left:232px;top:20px;font-size:5.5px;color:var(--ink-soft);line-height:12px}
.job .meta div{display:flex;align-items:center;gap:3px}
.job .sal{position:absolute;left:330px;top:17px;font-size:5.5px;color:var(--ink-soft);line-height:12px}
.job .sal strong{display:block;font-size:7px;font-weight:600;color:#5b5f62}
.job .actions{position:absolute;left:452px;top:19px;display:flex;gap:9px}
.job .mini{width:50px;height:19px;border-radius:10px;font-size:5px}
.scroll{position:absolute;width:2px;height:24px;background:#d4d4d4;border-radius:1px}
</style>
</head>
<body>

<div class="stage-decor" role="img" aria-label="Decorative green background artwork behind the app screens"></div>

<!-- Login version 1 -->
<h1 class="section-title" style="top:114px">Login Version 1</h1>
<section class="screen login-bg-1" style="top:160px">
  <div class="brand brand-lg" style="left:162px;top:72px">ZELVOR</div>
  <div class="login-card" style="left:92px;top:145px">
    <h2>Recruitment <span>Web App</span> Access</h2>
    <hr>
    <h3>Log in to your account</h3>
    <p>Welcome to John Doe, please put your login credentials below to start using the app</p>
    <label class="field-label">Email Address<em>*</em></label>
    <div class="input">
      <svg width="8" height="6" viewBox="0 0 8 6"><rect width="8" height="6" rx="1" fill="#6A6E71"/><path d="M0.5 0.8 4 3.4 7.5 0.8" stroke="#efefef" fill="none" stroke-width=".8"/></svg>
      Enter email address
    </div>
    <div class="btn-continue">CONTINUE<i><svg width="6" height="6" viewBox="0 0 6 6"><path d="M2 1 4 3 2 5" stroke="#6A6E71" fill="none" stroke-width=".9"/></svg></i></div>
  </div>
  <div class="photo" role="img" aria-label="Photo of a young man in a denim jacket sitting on a green cube with a laptop"
       style="left:419px;top:44px;width:409px;height:445px;background:linear-gradient(180deg,#dcdcdc 0%,#8aa0b8 35%,#5f7fa3 70%,#7cb83a 100%);border-radius:4px 0 0 0"></div>
</section>

<!-- Login version 2 -->
<h1 class="section-title" style="top:723px">Login Version 2</h1>
<section class="screen login-bg-2" style="top:769px">
  <div class="brand brand-lg" style="left:142px;top:80px">ZELVOR</div>
  <div class="login-card outlined" style="left:72px;top:147px">
    <h2>Recruitment <span>Web App</span> Access</h2>
    <hr>
    <h3>Log in to your account</h3>
    <p>Welcome to John Doe, please put your login credentials below to start using the app</p>
    <label class="field-label">Email Address<em>*</em></label>
    <div class="input">
      <svg width="8" height="6" viewBox="0 0 8 6"><rect width="8" height="6" rx="1" fill="#6A6E71"/><path d="M0.5 0.8 4 3.4 7.5 0.8" stroke="#efefef" fill="none" stroke-width=".8"/></svg>
      Enter email address
    </div>
    <div class="btn-continue">CONTINUE<i><svg width="6" height="6" viewBox="0 0 6 6"><path d="M2 1 4 3 2 5" stroke="#6A6E71" fill="none" stroke-width=".9"/></svg></i></div>
  </div>
  <div class="photo" role="img" aria-label="Photo of a man with glasses relaxing on a green beanbag while using a laptop"
       style="left:362px;top:105px;width:466px;height:390px;background:linear-gradient(160deg,#ffffff 0%,#e6e8ea 30%,#9aa0a6 55%,#9ed64e 80%,#7fbf2e 100%);border-radius:40px 0 0 0"></div>
</section>

<!-- Dashboard -->
<h1 class="section-title" style="top:1323px">Dashboard</h1>
<section class="screen app" style="top:1369px">
  <header class="app-header">
    <div class="brand brand-sm" style="left:14px;top:20px">ZELVOR</div>
    <span class="divider"></span>
    <div class="title"><span>ZELVOR</span> DASHBOARD</div>
    <div class="pill" style="left:630px"><svg width="8" height="7" viewBox="0 0 8 7"><rect y="1.5" width="8" height="5.5" rx="1" fill="#87C032"/><rect x="2.5" width="3" height="2" rx=".5" fill="none" stroke="#87C032" stroke-width=".8"/></svg>Jobs</div>
    <div class="pill" style="left:695px"><svg width="6" height="8" viewBox="0 0 6 8"><path d="M0 0h4l2 2v6H0z" fill="#87C032"/></svg>CV</div>
    <svg class="hicon" style="left:770px" width="11" height="12" viewBox="0 0 11 12"><path d="M5.5 1C3.5 1 2.5 2.6 2.5 4.5V7L1 9h9L8.5 7V4.5C8.5 2.6 7.5 1 5.5 1z" fill="#6A6E71"/><circle cx="5.5" cy="10.5" r="1.2" fill="#6A6E71"/><circle cx="8.5" cy="2" r="1.6" fill="#87C032"/></svg>
    <svg class="hicon" style="left:796px" width="12" height="12" viewBox="0 0 12 12"><circle cx="5" cy="3.5" r="2.5" fill="#6A6E71"/><path d="M0 11c0-3 2-4.5 5-4.5S10 8 10 11z" fill="#6A6E71"/><circle cx="10" cy="8" r="1.6" fill="#87C032"/></svg>
  </header>

  <aside class="card side">
    <div class="avatar"><div role="img" aria-label="Profile portrait of the candidate"></div></div>
    <div class="name">Daniel Morar</div>
    <div class="email">info@danielmorar.net</div>
    <dl class="facts"><dt>Phone:</dt><dd>+08 555 210 4471</dd><dt>Age:</dt><dd>30</dd><dt>Gender:</dt><dd>Male</dd></dl>
    <hr>
    <h4>Field of Expertise (Szakmaja):</h4><div class="val">Software Development</div>
    <hr>
    <h4>Highest Level of Education:</h4><div class="val">Master's in Computer Science</div>
    <hr>
    <h4>Languages:</h4>
    <div class="lang"><div class="lbl"><span>Romanian:</span><span>65%</span></div><div class="bar"><b style="width:57%"></b></div></div>
    <div class="lang"><div class="lbl"><span>Hungarian</span><span>100%</span></div><div class="bar"><b style="width:100%"></b></div></div>
    <div class="lang"><div class="lbl"><span>English</span><span>80%</span></div><div class="bar"><b style="width:82%"></b></div></div>
  </aside>
  <span class="scroll" style="left:168px;top:337px"></span>

  <main class="card bio">
    <h4>About me:</h4>
    <p>"Hello! I am Daniel, a software developer with over 15 years of experience in full-stack development, specializing in creating robust web and mobile applications. I am passionate about leveraging technology to solve real-world problems and am always eager to learn and adapt to new challenges."</p>
    <h4 style="margin-top:9px">Years of work experience: <span class="badge">15 YEARS</span></h4>
    <hr>
    <h4>Education:</h4>
    <ul class="edu">
      <li><span>Bachelor's Degree in Computer Science</span><span>Danube State University</span></li>
      <li><span>Master's Degree in Information Technology</span><span>Pannon Institute of Technology</span></li>
    </ul>
    <hr>
    <h4>Qualifications:</h4>
    <ul>
      <li>Certified Java Developer</li>
      <li>Cloud Certified Solutions Architect</li>
      <li>UX Design Professional Certificate</li>
    </ul>
    <hr style="margin-top:14px">
    <h4>Skills:</h4>
    <ul class="skills">
      <li><span>Programming Languages</span><span>Java, Python, JavaScript, SQL</span></li>
      <li><span>Frameworks &amp; Libraries</span><span>React, Angular, Node.js, Django</span></li>
      <li><span>Tools</span><span>Git, Docker, Jenkins, Kubernetes</span></li>
      <li><span>Soft Skills</span><span>Team Leadership, Project Management, Problem Solving, Communication</span></li>
      <li><span>Other</span><span>UX/UI Design, Cloud Computing, Machine Learning Basics</span></li>
    </ul>
    <hr style="margin-top:14px">
    <h4>Driver's license:</h4>
    <div class="txt">Yes – Class B (Eligible to drive cars and light vehicles)</div>
  </main>

  <aside class="card myjobs">
    <h4>MY JOBS</h4>
    <div class="tabs"><span class="on">2 Saved</span><span>12 Applied</span><span>Archived</span></div>
    <div class="saved">
      <span class="logo"><svg width="12" height="12"><circle cx="6" cy="6" r="5" fill="#3d8fd6"/></svg></span>
      <div class="t">Data Analyst</div><div class="d">Saved on 7 Dec</div>
      <svg class="more" width="3" height="9" viewBox="0 0 3 9"><circle cx="1.5" cy="1" r="1" fill="#6A6E71"/><circle cx="1.5" cy="4.5" r="1" fill="#6A6E71"/><circle cx="1.5" cy="8" r="1" fill="#6A6E71"/></svg>
      <p>Looking for a seasoned software engineer with a knack for...</p>
      <div class="btns"><span class="mini apply">APPLY</span><span class="mini view">VIEW JOB</span></div>
    </div>
    <div class="saved">
      <span class="logo"><svg width="12" height="12"><rect x="1" y="1" width="10" height="10" fill="#7a5cc8"/></svg></span>
      <div class="t">Product Manager</div><div class="d">Saved on 7 Dec</div>
      <svg class="more" width="3" height="9" viewBox="0 0 3 9"><circle cx="1.5" cy="1" r="1" fill="#6A6E71"/><circle cx="1.5" cy="4.5" r="1" fill="#6A6E71"/><circle cx="1.5" cy="8" r="1" fill="#6A6E71"/></svg>
      <p>Seeking a data-driven analyst to interpret complex data sets...</p>
      <div class="btns"><span class="mini apply">APPLY</span><span class="mini view">VIEW JOB</span></div>
    </div>
  </aside>
</section>

<!-- Jobs -->
<h1 class="section-title" style="top:1932px">Jobs</h1>
<section class="screen app" style="top:1977px">
  <header class="app-header">
    <div class="brand brand-sm" style="left:14px;top:20px">ZELVOR</div>
    <span class="divider"></span>
    <div class="title">JOBS</div>
    <div class="pill" style="left:630px"><svg width="8" height="7" viewBox="0 0 8 7"><rect y="1.5" width="8" height="5.5" rx="1" fill="#87C032"/><rect x="2.5" width="3" height="2" rx=".5" fill="none" stroke="#87C032" stroke-width=".8"/></svg>Jobs</div>
    <div class="pill" style="left:695px"><svg width="6" height="8" viewBox="0 0 6 8"><path d="M0 0h4l2 2v6H0z" fill="#87C032"/></svg>CV</div>
    <svg class="hicon" style="left:770px" width="11" height="12" viewBox="0 0 11 12"><path d="M5.5 1C3.5 1 2.5 2.6 2.5 4.5V7L1 9h9L8.5 7V4.5C8.5 2.6 7.5 1 5.5 1z" fill="#6A6E71"/><circle cx="5.5" cy="10.5" r="1.2" fill="#6A6E71"/><circle cx="8.5" cy="2" r="1.6" fill="#87C032"/></svg>
    <svg class="hicon" style="left:796px" width="12" height="12" viewBox="0 0 12 12"><circle cx="5" cy="3.5" r="2.5" fill="#6A6E71"/><path d="M0 11c0-3 2-4.5 5-4.5S10 8 10 11z" fill="#6A6E71"/><circle cx="10" cy="8" r="1.6" fill="#87C032"/></svg>
  </header>

  <aside class="card side" style="top:66px">
    <div class="avatar"><div role="img" aria-label="Profile portrait of the candidate"></div></div>
    <div class="name">Daniel Morar</div>
    <div class="email">info@danielmorar.net</div>
    <dl class="facts"><dt>Phone:</dt><dd>+08 555 210 4471</dd><dt>Age:</dt><dd>30</dd><dt>Gender:</dt><dd>Male</dd></dl>
    <hr>
    <h4>Field of Expertise (Szakmaja):</h4><div class="val">Software Development</div>
    <hr>
    <h4>Highest Level of Education:</h4><div class="val">Master's in Computer Science</div>
    <hr>
    <h4>Languages:</h4>
    <div class="lang"><div class="lbl"><span>Romanian:</span><span>65%</span></div><div class="bar"><b style="width:57%"></b></div></div>
    <div class="lang"><div class="lbl"><span>Hungarian</span><span>100%</span></div><div class="bar"><b style="width:100%"></b></div></div>
    <div class="lang"><div class="lbl"><span>English</span><span>80%</span></div><div class="bar"><b style="width:82%"></b></div></div>
  </aside>
  <span class="scroll" style="left:168px;top:338px"></span>

  <main class="card jobs-main" style="top:66px">
    <div class="search">Enter filter keyword
      <svg width="8" height="8" viewBox="0 0 8 8"><circle cx="3.3" cy="3.3" r="2.5" fill="none" stroke="#5b5f62" stroke-width=".9"/><path d="M5.2 5.2 7.5 7.5" stroke="#5b5f62" stroke-width=".9"/></svg>
    </div>
    <div class="tools">
      <span><svg width="8" height="8" viewBox="0 0 8 8" fill="none" stroke="#6A6E71" stroke-width=".8"><rect x=".5" y=".5" width="3" height="3"/><rect x="4.5" y=".5" width="3" height="3"/><rect x=".5" y="4.5" width="3" height="3"/><rect x="4.5" y="4.5" width="3" height="3"/></svg></span>
      <span class="on"><svg width="8" height="7" viewBox="0 0 8 7" stroke="#fff" stroke-width=".9"><path d="M0 1h8M0 3.5h8M0 6h5"/></svg></span>
      <span><svg width="8" height="8" viewBox="0 0 8 8"><path d="M.5 .8h7L4.8 4.2V7.3L3.2 6.4V4.2z" fill="none" stroke="#6A6E71" stroke-width=".8"/></svg></span>
      <span><svg width="8" height="8" viewBox="0 0 8 8"><path d="M6.8 4A2.8 2.8 0 1 1 5.9 1.9" fill="none" stroke="#6A6E71" stroke-width=".9"/><path d="M5 .6 6.4 1.9 5 3" fill="none" stroke="#6A6E71" stroke-width=".9"/></svg></span>
      <span><svg width="3" height="9" viewBox="0 0 3 9"><circle cx="1.5" cy="1" r="1" fill="#6A6E71"/><circle cx="1.5" cy="4.5" r="1" fill="#6A6E71"/><circle cx="1.5" cy="8" r="1" fill="#6A6E71"/></svg></span>
    </div>

    <div class="joblist">
      <div class="job">
        <span class="logo" style="--c:#7b5ccf"><b></b></span>
        <div class="co">Nexora Labs</div><div class="role">Full Stack Developer E-commerce</div>
        <div class="meta"><div><svg width="5" height="6" viewBox="0 0 5 6"><path d="M2.5 6S0 3.6 0 2.3a2.5 2.5 0 0 1 5 0C5 3.6 2.5 6 2.5 6z" fill="#6A6E71"/></svg>Seattle, USA</div><div><svg width="5" height="5"><circle cx="2.5" cy="2.5" r="2.5" fill="#6A6E71"/></svg>Full-time</div></div>
        <div class="sal"><strong>Salary</strong>€60,000 – €75,000 per year</div>
        <div class="actions"><span class="mini view">VIEW MORE</span><span class="mini apply">APPLY</span></div>
      </div>
      <div class="job">
        <span class="logo" style="--c:#c9b83a"><b></b></span>
        <div class="co">Lumeva Capital</div><div class="role">Product Manager – FinTech</div>
        <div class="meta"><div><svg width="5" height="6" viewBox="0 0 5 6"><path d="M2.5 6S0 3.6 0 2.3a2.5 2.5 0 0 1 5 0C5 3.6 2.5 6 2.5 6z" fill="#6A6E71"/></svg>London, UK</div><div><svg width="5" height="5"><circle cx="2.5" cy="2.5" r="2.5" fill="#6A6E71"/></svg>Part-time</div></div>
        <div class="sal"><strong>Salary</strong>£45,000 – £60,000 per year</div>
        <div class="actions"><span class="mini view">VIEW MORE</span><span class="mini apply">APPLY</span></div>
      </div>
      <div class="job hl">
        <span class="logo" style="--c:#3c5db5"><b></b></span>
        <div class="co">Quantile Metrics</div><div class="role">Data Engineer Analytics Platform</div>
        <div class="meta"><div><svg width="5" height="6" viewBox="0 0 5 6"><path d="M2.5 6S0 3.6 0 2.3a2.5 2.5 0 0 1 5 0C5 3.6 2.5 6 2.5 6z" fill="#6A6E71"/></svg>Dublin, Ireland</div><div><svg width="5" height="5"><circle cx="2.5" cy="2.5" r="2.5" fill="#6A6E71"/></svg>Full-time</div></div>
        <div class="sal"><strong>Salary</strong>€55,000 – €70,000 per year</div>
        <div class="actions"><span class="mini view">VIEW MORE</span><span class="mini apply">APPLY</span></div>
      </div>
      <div class="job">
        <span class="logo" style="--c:#d8343f"><b></b></span>
        <div class="co">Solvane Tech</div><div class="role">UX/UI Designer – SaaS Product</div>
        <div class="meta"><div><svg width="5" height="6" viewBox="0 0 5 6"><path d="M2.5 6S0 3.6 0 2.3a2.5 2.5 0 0 1 5 0C5 3.6 2.5 6 2.5 6z" fill="#6A6E71"/></svg>Remote</div><div><svg width="5" height="5"><circle cx="2.5" cy="2.5" r="2.5" fill="#6A6E71"/></svg>Full-time</div></div>
        <div class="sal"><strong>Salary</strong>$50 – $70 per hour</div>
        <div class="actions"><span class="mini view">VIEW MORE</span><span class="mini apply">APPLY</span></div>
      </div>
      <div class="job">
        <span class="logo" style="--c:#e49a2f"><b></b></span>
        <div class="co">Vaporine</div><div class="role">Backend Developer – Cloud</div>
        <div class="meta"><div><svg width="5" height="6" viewBox="0 0 5 6"><path d="M2.5 6S0 3.6 0 2.3a2.5 2.5 0 0 1 5 0C5 3.6 2.5 6 2.5 6z" fill="#6A6E71"/></svg>Seattle, USA</div><div><svg width="5" height="5"><circle cx="2.5" cy="2.5" r="2.5" fill="#6A6E71"/></svg>Full-time</div></div>
        <div class="sal"><strong>Salary</strong>$80,000 – $100,000 per year</div>
        <div class="actions"><span class="mini view">VIEW MORE</span><span class="mini apply">APPLY</span></div>
      </div>
    </div>
    <span class="scroll" style="left:609px;top:270px"></span>
  </main>
</section>

</body>
</html>
```